Color Revisions on Page File

We need the colors in the attached "New Profile View" file revised to match and flow seamlessly with our new Home Page (attached file "New Home").
Source file for Profile View attached as well.
We do not need any page elements re-positioned. This is all about optimizing colors to ensure a nice modern look and consistent navigation.
You only need to submit top half of the page until winner is selected. This will prevent unnecessary work on your end. Upon selection, you can complete the makeover.
Please submit your best design at earliest possible, as this is a rush project. Thanks greatly!
Please focus on the lighter colors with only dark attributes. This new look should be fresh and crisp - with an appearance comparable to best-in-class solutions. Thanks.
PLEASE NOTE: I have just uploaded another file called "Sample5". Please use similar color scheme to this in your design. Thank you!

```html
<!DOCTYPE html>
<html lang="en">
<head>
<meta charset="utf-8">
<title>ReachMetric – Influencer Profile</title>
<link href="https://fonts.googleapis.com/css2?family=Open+Sans:wght@400;600;700;800&family=Oswald:wght@400;600&display=swap" rel="stylesheet">
<style>
:root{
  --page:#eceeef;
  --card:#ffffff;
  --line:#d9dcde;
  --soft:#f5f6f7;
  --ink:#3c4247;
  --muted:#8a9196;
  --dark:#2f3439;
  --blue:#2d9bd6;
  --navy:#3b5a9a;
  --pro:#1f78b4;
  --green:#6cb33f;
  --red:#e0452f;
  --orange:#f39a1e;
  --teal:#4fb7a9;
}
*{box-sizing:border-box;margin:0;padding:0}
html,body{width:1200px;height:2904px;overflow:hidden}
body{background:var(--page);font-family:"Open Sans",Arial,sans-serif;color:var(--ink);font-size:15px;line-height:1.35}
.page{width:1200px;height:2904px;position:relative}
.site-header{height:84px;background:var(--card);border-bottom:1px solid var(--line);display:flex;align-items:center;justify-content:space-between;padding:0 36px}
.brand{display:flex;align-items:center;gap:12px}
.brand-dot{width:22px;height:22px;border-radius:50%;background:var(--blue)}
.brand-name{font-weight:700;font-size:34px;color:var(--dark)}
.brand-tag{font-size:12px;color:var(--muted);margin-top:2px}
.account-bar{height:56px;background:var(--dark);color:#dfe3e6;display:flex;align-items:center;justify-content:space-between;padding:0 36px;font-size:13px}
.account-bar b{color:#fff}
.complete{background:var(--blue);color:#fff;padding:6px 14px;font-weight:700;font-size:12px}
.wrap{padding:0 20px}
.profile{height:380px;background:var(--card);border:1px solid var(--line);margin-top:12px;display:flex}
.p-info{width:300px;padding:18px 20px;border-right:1px solid var(--line);font-size:13px}
.p-info h4{font-size:13px;margin-top:14px;color:var(--dark)}
.p-info p{color:var(--muted)}
.p-social{width:470px;padding:14px 18px;border-right:1px solid var(--line)}
.p-head{display:flex;gap:12px;align-items:center;margin-bottom:10px}
.photo{width:70px;height:70px;background:linear-gradient(#cfd5da,#a9b2b9)}
.p-head b{color:var(--blue);font-size:15px}
.net{display:flex;align-items:center;gap:12px;border:1px solid var(--line);background:var(--soft);padding:8px 12px;margin-bottom:8px;height:84px}
.net-name{width:86px;font-weight:700;font-size:14px}
.net-stats{flex:1;font-size:12px;color:var(--muted)}
.net-stats span{display:block}
.bar{display:inline-block;background:var(--blue);color:#fff;font-size:11px;padding:2px 8px;margin:2px 0}
.connect{background:var(--green);color:#fff;font-weight:700;padding:10px 26px;font-size:14px}
.p-strength{flex:1;padding:22px 30px;display:flex;flex-direction:column;align-items:center}
.s-label{font-size:14px;color:var(--muted);align-self:flex-start}
.s-title{font-family:"Oswald",sans-serif;font-size:54px;letter-spacing:4px;color:var(--dark);align-self:flex-start;line-height:1}
.s-row{display:flex;gap:30px;align-items:center;margin-top:18px}
.s-nums{font-size:15px;line-height:1.9}
.s-nums b{color:var(--blue)}
.ranking{margin-top:16px;color:var(--muted);font-size:14px}
.actions{height:40px;display:flex;justify-content:space-between;align-items:center;margin-top:6px}
.btn{background:var(--dark);color:#fff;font-size:12px;padding:6px 16px;margin-right:6px;display:inline-block}
.ico{display:inline-block;width:24px;height:24px;background:var(--dark);margin-left:4px}
.links{height:130px;background:var(--card);border:1px solid var(--line);padding:14px 20px;font-size:13px;color:var(--blue);line-height:1.8}
.card{background:var(--card);border:1px solid var(--line);margin-top:12px}
.card-head{height:40px;display:flex;align-items:center;gap:10px;padding:0 16px;color:#fff;font-weight:700;font-size:17px}
.card-head i{width:22px;height:22px;background:rgba(255,255,255,.9);display:inline-block}
.h-chirp{background:var(--blue)}
.h-circle{background:var(--navy)}
.h-pro{background:var(--pro)}
.cols{display:flex;gap:16px;padding:16px}
.col{flex:1}
.col h5{font-size:14px;color:var(--dark);margin-bottom:8px;padding-bottom:6px;border-bottom:2px solid var(--line)}
.stat{display:flex;justify-content:space-between;align-items:center;border-bottom:1px solid var(--line);padding:6px 0;font-size:13px}
.stat i{width:14px;height:14px;background:var(--red);display:inline-block;margin-right:8px;vertical-align:middle}
.stat b{color:var(--dark)}
.box{border:1px solid var(--line);background:var(--soft);height:110px;padding:8px 10px;font-size:12px;color:var(--muted);line-height:1.7}
.legend{font-size:12px;line-height:1.9}
.legend i{width:10px;height:10px;display:inline-block;margin-right:6px}
.pct{display:flex;justify-content:space-around;font-size:22px;font-weight:700;margin-top:10px}
.dots{display:flex;justify-content:space-between;padding:6px 4px}
.dot{text-align:center;font-size:11px;color:var(--muted)}
.dot div{width:44px;height:44px;border-radius:50%;background:var(--red);color:#fff;font-weight:700;display:flex;align-items:center;justify-content:center;font-size:12px;margin:0 auto 4px;border:3px solid #f3c1b9}
.pie-row{display:flex;align-items:center;gap:12px}
.job{display:flex;justify-content:space-between;border-bottom:1px solid var(--line);padding:8px 0;font-size:13px}
.job small{color:var(--muted);display:block}
.rec{padding:10px 16px;font-size:12px;color:var(--muted);line-height:1.6}
.rec b{color:var(--dark)}
.site-footer{position:absolute;left:0;right:0;bottom:0;height:130px;border-top:1px solid var(--line);background:var(--card);text-align:center;padding-top:34px}
.f-links{display:flex;justify-content:center;gap:70px;font-size:13px;font-weight:700;color:var(--muted)}
.copy{font-size:11px;color:var(--muted);margin-top:34px}
</style>
</head>
<body>
<div class="page">
<header class="site-header">
  <div class="brand"><span class="brand-dot"></span><div><div class="brand-name">ReachMetric</div><div class="brand-tag">The social influence marketplace</div></div></div>
  <svg width="30" height="30" viewBox="0 0 30 30"><circle cx="15" cy="15" r="10" fill="none" stroke="#3c4247" stroke-width="6" stroke-dasharray="4 3"/><circle cx="15" cy="15" r="4" fill="#3c4247"/></svg>
</header>
<div class="account-bar"><span><b>My account</b> &nbsp;|&nbsp; Manage your profile, campaigns and settings in one place</span><span class="complete">PROFILE 80% COMPLETE</span></div>

<div class="wrap">
<section class="profile">
  <div class="p-info">
    <b>Location: New York</b>
    <p>Position: Full time, Part time &amp; Freelance</p>
    <h4>Industries, Topics in Focus</h4>
    <p>Marketing · Media · Lifestyle</p>
    <p>Technology · Business</p>
    <h4>Promotion Experience</h4>
    <p>Radio: 2 / 5 years</p><p>Television: 3 / 5 years</p><p>Print: 4 / 5 years</p>
    <h4>Language Known</h4>
    <p>English · Spanish · French</p>
  </div>
  <div class="p-social">
    <div class="p-head"><div class="photo" role="img" aria-label="Profile photo"></div><div><b>Sample profile name</b><br><span style="font-size:12px;color:#8a9196">Engineer and creative strategist</span></div></div>
    <div class="net"><span class="net-name">Chirper</span><div class="net-stats"><span>Account since 03/2009</span><span>Followers <b>9,841</b></span></div>
      <svg width="60" height="60"><circle cx="30" cy="30" r="24" fill="none" stroke="#d9dcde" stroke-width="7"/><circle cx="30" cy="30" r="24" fill="none" stroke="#2d9bd6" stroke-width="7" stroke-dasharray="48 151" transform="rotate(-90 30 30)"/><text x="30" y="35" text-anchor="middle" font-size="14" font-weight="700" fill="#2f3439">32%</text></svg></div>
    <div class="net"><span class="net-name">Circlebook</span><div class="net-stats"><span class="bar">Total Friends 1,234</span><br><span class="bar">Page Likes 3,210</span></div>
      <svg width="120" height="60"><circle cx="30" cy="30" r="24" fill="none" stroke="#d9dcde" stroke-width="7"/><circle cx="30" cy="30" r="24" fill="none" stroke="#3b5a9a" stroke-width="7" stroke-dasharray="95 151" transform="rotate(-90 30 30)"/><text x="30" y="35" text-anchor="middle" font-size="14" font-weight="700" fill="#2f3439">63%</text><circle cx="90" cy="30" r="24" fill="none" stroke="#d9dcde" stroke-width="7"/><circle cx="90" cy="30" r="24" fill="none" stroke="#3b5a9a" stroke-width="7" stroke-dasharray="127 151" transform="rotate(-90 90 30)"/><text x="90" y="35" text-anchor="middle" font-size="14" font-weight="700" fill="#2f3439">84%</text></svg></div>
    <div class="net"><span class="net-name">ProLink</span><div class="net-stats">Login to connect your account</div><span class="connect">CONNECT NOW</span></div>
  </div>
  <div class="p-strength">
    <span class="s-label">Influence</span>
    <span class="s-title">STRENGTH</span>
    <div class="s-row">
      <div class="s-nums">B/T: <b>75.8</b><br>B2: <b>48.2</b><br>AVG: <b>45.6</b></div>
      <svg width="170" height="170"><circle cx="85" cy="85" r="70" fill="#f5f6f7" stroke="#d9dcde" stroke-width="14"/><circle cx="85" cy="85" r="70" fill="none" stroke="#2d9bd6" stroke-width="14" stroke-dasharray="97 440" transform="rotate(-90 85 85)"/><text x="85" y="97" text-anchor="middle" font-size="36" font-weight="700" fill="#2f3439">22%</text></svg>
    </div>
    <div class="ranking">ranking <b>22</b> / 100%</div>
  </div>
</section>

<div class="actions"><div><span class="btn">Likes</span><span class="btn">Resume</span></div><div><span class="ico"></span><span class="ico"></span><span class="ico"></span><span class="ico"></span><span class="ico"></span></div></div>

<div class="links">www.sampleblog.com<br>www.samplefeed.net/profile<br>www.portfolio-sample.org<br>www.sampleshop.com/store</div>

<section class="card" style="height:448px">
  <div class="card-head h-chirp"><i></i>Chirper</div>
  <div class="cols">
    <div class="col"><h5>Account</h5>
      <div class="stat"><span><i></i>Followers</span><b>9,841</b></div>
      <div class="stat"><span><i></i>Updates sent</span><b>3,157</b></div>
      <div class="stat"><span><i></i>Lists</span><b>1,204</b></div>
      <div class="stat"><span><i></i>Interaction received</span><b>6,214</b></div>
    </div>
    <div class="col"><h5>Outreach by @sampleuser</h5>
      <div class="stat"><span><i style="background:var(--blue)"></i>Following</span><b>6,295</b></div>
      <div class="stat"><span><i style="background:var(--blue)"></i>@/Mentions</span><b>1,476</b></div>
      <div class="stat"><span><i style="background:var(--blue)"></i>Links posted</span><b>2,314</b></div>
      <div class="stat"><span><i style="background:var(--blue)"></i>Interaction sent</span><b>6,214</b></div>
    </div>
    <div class="col"><h5>Follower Validation</h5>
      <div class="pct"><span style="color:var(--red)">0%</span><span style="color:var(--orange)">25%</span><span style="color:var(--green)">75%</span></div>
      <div class="legend" style="margin-top:10px"><i style="background:var(--green)"></i>Validated followers with real activity<br><i style="background:var(--orange)"></i>Partially active followers<br><i style="background:var(--red)"></i>Inactive or unverified followers</div>
    </div>
  </div>
  <div class="cols" style="padding-top:0">
    <div class="col"><h5>Most Mentioned</h5><div class="box">Short sample mention text<br>Another sample mention here<br>Third sample mention line</div></div>
    <div class="col"><h5>Most Used</h5><div class="box">Sample tag one used often<br>Sample tag two used often<br>Sample tag three used often</div></div>
    <div class="col"><h5>Most posted links</h5><div class="box">www.samplelink-one.com<br>www.samplelink-two.com<br>www.samplelink-three.com</div></div>
  </div>
</section>

<section class="card" style="height:830px">
  <div class="card-head h-circle"><i></i>Circlebook</div>
  <div class="cols">
    <div class="col"><h5>Activity</h5>
      <div class="stat"><span><i></i>Uploaded photos</span><b>188</b></div>
      <div class="stat"><span><i></i>Comments</span><b>54</b></div>
      <div class="stat"><span><i></i>Pictures</span><b>290</b></div>
    </div>
    <div class="col"><h5>Post statistics</h5>
      <div class="stat"><span><i style="background:var(--navy)"></i>Total posts</span><b>932</b></div>
      <div class="stat"><span><i style="background:var(--navy)"></i>Total likes</span><b>1,860</b></div>
      <div class="stat"><span><i style="background:var(--navy)"></i>Average post length</span><b>4 words, 36 chars</b></div>
    </div>
    <div class="col"><h5>Most Mentioned</h5><div class="box" style="height:100px">Sample mention text line one<br>Sample mention text line two<br>Sample mention text line three</div>
      <div class="stat"><span><i></i>Followers</span><b>5,641</b></div></div>
  </div>
  <div class="cols" style="padding-top:0">
    <div class="col"><h5>Friends' Top Countries</h5><div class="dots"><div class="dot"><div>42%</div>USA</div><div class="dot"><div>18%</div>UK</div><div class="dot"><div>12%</div>CAN</div><div class="dot"><div>8%</div>AUS</div></div></div>
    <div class="col"><h5>Friends' Top States</h5><div class="dots"><div class="dot"><div>34%</div>NY</div><div class="dot"><div>21%</div>CA</div><div class="dot"><div>14%</div>TX</div><div class="dot"><div>9%</div>WI</div></div></div>
    <div class="col"><h5>Friends' Top Cities</h5><div class="dots"><div class="dot"><div>28%</div>Minneapolis</div><div class="dot"><div>19%</div>San Francisco</div><div class="dot"><div>11%</div>Milwaukee</div></div></div>
  </div>
  <div class="cols" style="padding-top:10px">
    <div class="col"><h5>Friends' Gender</h5><div class="pie-row">
      <svg width="150" height="150"><circle cx="75" cy="75" r="60" fill="#3b5a9a"/><circle cx="75" cy="75" r="30" fill="none" stroke="#9fc6e8" stroke-width="60" stroke-dasharray="85 189" transform="rotate(-90 75 75)"/></svg>
      <div class="legend"><i style="background:#3b5a9a"></i>Male<br><i style="background:#9fc6e8"></i>Female</div></div></div>
    <div class="col"><h5>Friends' Relationship</h5><div class="pie-row">
      <svg width="150" height="150"><circle cx="75" cy="75" r="60" fill="#9fc6e8"/><circle cx="75" cy="75" r="30" fill="none" stroke="#3b5a9a" stroke-width="60" stroke-dasharray="70 189" transform="rotate(-90 75 75)"/><circle cx="75" cy="75" r="30" fill="none" stroke="#2d9bd6" stroke-width="60" stroke-dasharray="40 189" stroke-dashoffset="-70" transform="rotate(-90 75 75)"/></svg>
      <div class="legend"><i style="background:#3b5a9a"></i>Married<br><i style="background:#2d9bd6"></i>Single<br><i style="background:#9fc6e8"></i>Engaged<br><i style="background:#d9dcde"></i>Other</div></div></div>
    <div class="col"><h5>Friends' Age</h5><div class="pie-row">
      <svg width="150" height="150"><circle cx="75" cy="75" r="60" fill="#9fc6e8"/><circle cx="75" cy="75" r="30" fill="none" stroke="#2d9bd6" stroke-width="60" stroke-dasharray="60 189" transform="rotate(-90 75 75)"/><circle cx="75" cy="75" r="30" fill="none" stroke="#3b5a9a" stroke-width="60" stroke-dasharray="45 189" stroke-dashoffset="-60" transform="rotate(-90 75 75)"/></svg>
      <div class="legend"><i style="background:#2d9bd6"></i>18–24<br><i style="background:#3b5a9a"></i>25–34<br><i style="background:#9fc6e8"></i>35–44<br><i style="background:#d9dcde"></i>45+</div></div></div>
  </div>
</section>

<section class="card" style="height:724px">
  <div class="card-head h-pro"><i></i>ProLink</div>
  <div class="cols">
    <div class="col" style="flex:2"><h5>Most Recent Employment Positions</h5>
      <div class="job"><span><b>Chief Operating Officer</b><small>Northfield Group</small></span><span>Oct 2011 – Present<small>New York, NY</small></span></div>
      <div class="job"><span><b>Content Licensing Manager</b><small>Brightline Media</small></span><span>May 2009 – Sep 2011<small>Boston, MA</small></span></div>
      <div class="job"><span><b>Marketing Manager</b><small>Harbor Creative Partners</small></span><span>Feb 2007 – Apr 2009<small>Chicago, IL</small></span></div>
      <div class="job"><span><b>Strategic Business Consultant</b><small>Summit Advisory Co.</small></span><span>Jan 2005 – Jan 2007<small>Houston, TX</small></span></div>
      <div class="job"><span><b>Brand Manager</b><small>Westgate Retail</small></span><span>Jun 2003 – Dec 2004<small>Denver, CO</small></span></div>
    </div>
    <div class="col"><h5>Industry of Contacts</h5><div class="pie-row">
      <svg width="150" height="150"><circle cx="75" cy="75" r="60" fill="#9fc6e8"/><circle cx="75" cy="75" r="30" fill="none" stroke="#1f78b4" stroke-width="60" stroke-dasharray="75 189" transform="rotate(-90 75 75)"/><circle cx="75" cy="75" r="30" fill="none" stroke="#4fb7a9" stroke-width="60" stroke-dasharray="40 189" stroke-dashoffset="-75" transform="rotate(-90 75 75)"/></svg>
      <div class="legend"><i style="background:#1f78b4"></i>Printing<br><i style="background:#4fb7a9"></i>Publishing<br><i style="background:#9fc6e8"></i>Advertising<br><i style="background:#d9dcde"></i>Other</div></div>
      <h5 style="margin-top:16px">Location of Contacts</h5><div class="pie-row">
      <svg width="150" height="150"><circle cx="75" cy="75" r="60" fill="#9fc6e8"/><circle cx="75" cy="75" r="30" fill="none" stroke="#1f78b4" stroke-width="60" stroke-dasharray="90 189" transform="rotate(-90 75 75)"/></svg>
      <div class="legend"><i style="background:#1f78b4"></i>New York<br><i style="background:#9fc6e8"></i>Other cities</div></div>
    </div>
  </div>
  <div class="cols" style="padding-top:0">
    <div class="col"><h5>Skills</h5><div class="box" style="height:70px">Marketing · Branding · Strategy<br>Licensing · Public Relations</div></div>
    <div class="col"><h5>Groups</h5><div class="box" style="height:70px">Media Professionals Network<br>Brand Strategy Forum</div></div>
  </div>
  <div class="rec"><b style="font-size:14px">Recommendations</b> (Received 4 of 10)<br><br>
    <b>Dana Whitfield</b> · Programmer, Northfield Group<br>Reliable and thoughtful partner who delivers strong results on every project and keeps teams focused on what matters.<br><br>
    <b>Owen Castell</b> · Designer, Brightline Media<br>A clear communicator with great ideas, always organized and quick to solve problems under tight deadlines.</div>
</section>
</div>

<footer class="site-footer">
  <div class="f-links"><span>SAMPLE PROFILE</span><span>CONTACT US</span><span>TERMS &amp; CONDITIONS</span><span>PRIVACY POLICY</span></div>
  <div class="copy">Copyright © 2013 ReachMetric. All rights reserved.</div>
</footer>
</div>
</body>
</html>
```